BildeVOLD buisnesscard

Hey :) I need a modern buisnesscard for my company BildeVOLD
It most have:
Dagligleder og Fotograf: Henrik Audun Strandvik

Mob: +4791264085
Epost: post@bildevold.example
Adresse: Kvernbakken9, 6040 Langevåg

Facbook and instagram logo with text BildeVOLD

BildeVOLD logo

It Company

```html
<!DOCTYPE html>
<html lang="no">
<head>
<meta charset="utf-8">
<title>BildeVOLD – visittkort</title>
<link href="https://fonts.googleapis.com/css2?family=Lato:wght@400;700&display=swap" rel="stylesheet">
<style>
  :root {
    --page-bg: #e6e6e6;
    --card-white: #ffffff;
    --card-black: #050505;
    --brand-grey: #b4b2b3;
    --text-dark: #111111;
    --text-muted: #b9b9b9;
    --icon-grey: #9a9a9a;
  }
  * { margin: 0; padding: 0; box-sizing: border-box; }
  html, body { width: 1200px; height: 900px; overflow: hidden; }
  body {
    background: var(--page-bg);
    font-family: "Lato", Arial, sans-serif;
    display: flex;
    align-items: center;
    justify-content: center;
    gap: 60px;
  }
  .card {
    width: 520px;
    height: 297px;
    position: relative;
    box-shadow: 0 6px 18px rgba(0,0,0,.18);
  }
  .card--back {
    background: var(--card-black);
    display: flex;
    align-items: center;
    justify-content: center;
  }
  .card--front { background: var(--card-white); }

  .brand {
    display: flex;
    align-items: center;
    gap: 12px;
    color: var(--brand-grey);
    font-weight: 700;
    letter-spacing: .5px;
  }
  .brand__mark {
    background: var(--brand-grey);
    display: block;
  }
  .card--back .brand { font-size: 54px; }
  .card--back .brand__mark { width: 40px; height: 40px; }

  .card--front .brand {
    position: absolute;
    left: 34px;
    top: 40px;
    font-size: 44px;
  }
  .card--front .brand__mark { width: 32px; height: 32px; }

  .holder {
    position: absolute;
    left: 38px;
    top: 122px;
  }
  .holder__name {
    font-size: 19px;
    font-weight: 400;
    color: var(--text-dark);
    letter-spacing: .4px;
    text-transform: uppercase;
  }
  .holder__title {
    font-size: 15px;
    color: var(--text-muted);
    margin-top: 2px;
  }

  .contact {
    position: absolute;
    left: 318px;
    top: 168px;
    color: var(--text-dark);
    font-size: 15px;
    line-height: 19px;
  }
  .contact__address { margin-bottom: 8px; }
  .contact__list { list-style: none; }
  .contact__item { display: flex; align-items: center; gap: 8px; }
  .contact__icon { width: 12px; height: 12px; flex: none; }
</style>
</head>
<body>
  <section class="card card--back" aria-label="Visittkort bakside">
    <div class="brand">
      <span class="brand__mark"></span>
      <span class="brand__name">BildeVOLD</span>
    </div>
  </section>

  <section class="card card--front" aria-label="Visittkort forside">
    <div class="brand">
      <span class="brand__mark"></span>
      <span class="brand__name">BildeVOLD</span>
    </div>

    <div class="holder">
      <p class="holder__name">Henrik Audun Strandvik</p>
      <p class="holder__title">Dagligleder og Fotograf</p>
    </div>

    <div class="contact">
      <p class="contact__address">Kvernbakken 9<br>6040 Fjordvik</p>
      <ul class="contact__list">
        <li class="contact__item">
          <svg class="contact__icon" viewBox="0 0 12 12" aria-hidden="true">
            <rect x="3" y="0.5" width="6" height="11" rx="1" fill="none" stroke="var(--icon-grey)" stroke-width="1.2"/>
            <circle cx="6" cy="9.5" r=".8" fill="var(--icon-grey)"/>
          </svg>
          <span>+4791264085</span>
        </li>
        <li class="contact__item">
          <svg class="contact__icon" viewBox="0 0 12 12" aria-hidden="true">
            <rect x="0.5" y="2" width="11" height="8" fill="none" stroke="var(--icon-grey)" stroke-width="1.2"/>
            <path d="M.5 2 6 7 11.5 2" fill="none" stroke="var(--icon-grey)" stroke-width="1.2"/>
          </svg>
          <span>post@bildevold.example</span>
        </li>
        <li class="contact__item">
          <svg class="contact__icon" viewBox="0 0 12 12" aria-hidden="true">
            <rect x="0.5" y="0.5" width="11" height="11" fill="var(--icon-grey)"/>
          </svg>
          <span>BildeVOLD</span>
        </li>
        <li class="contact__item">
          <svg class="contact__icon" viewBox="0 0 12 12" aria-hidden="true">
            <circle cx="6" cy="6" r="5.5" fill="var(--icon-grey)"/>
          </svg>
          <span>BildeVOLD</span>
        </li>
      </ul>
    </div>
  </section>
</body>
</html>
```